Business Cards for IT Consulting Company (Managed Service Provider)

I am looking to have some business cards printed and would like some designs. We are an IT Consulting company based in Vancouver BC. I would like a nice clean and modern look to the cards. I have uploaded all the versions of my logo so parts can be used as needed. Here is a snippit from our website homepage:

Quillbrook Networks Ltd. is an IT Solutions Partner located in Vancouver BC, Canada. We offer IT solutions and support to customers in the greater Vancouver Area. With expertise in Microsoft platforms, as well as Linux and Mac OSX and over 12 years experience in the IT industry, Quillbrook Networks is dedicated to offering our clients top quality service and products. We take pride in the solutions we offer our customers. The greatest compliment a client can give us is to recommend our services.

Quillbrook Networks Ltd. offers a wide range of IT services from onsite service to remote support and managed service solutions. This allows clients to choose the support path that best suits their company’s needs. Supporting many different sized companies from small to enterprise level over the past 12 years Quillbrook Networks has the experience and expertise needed to ensure things run smoothly. Allowing our clients to focus on doing business.

Revolutionizing the way IT services are delivered.

Quillbrook Networks is dedicated to providing our clients with IT solutions that work and grow with them for years to come. This philosophy helps save money in the long run instead of replacing equipment constantly. Far too often IT solutions are not well thought out and while possibly solving the problem at hand, require replacement due to growth or quality within a very short time frame. Quillbrook Networks takes pride in providing solutions that will last and be able to accommodate growth without the need for replacement.

Industry/Entity Type

Information Technology

Contact Information for Business Card

Quillbrook Networks Ltd.
(Employee Name)
Eml: (Employees Email Address)
Web: quillbrook.me
Ph: 604-555-0148

Font styles to use
Serif
Sans Serif

Requirements
Must have
• The Company logo and company colors.
Nice to have
• - Our tag line: "Revolutionizing IT Services" or "Revolutionizing the way IT services are delivered."
• - Also I really like the idea of nature and technology together blending which is sort of where my logo came from so integrating that somehow onto the business cards would be great.

```html
<!DOCTYPE html>
<html lang="en">
<head>
<meta charset="utf-8">
<title>Quillbrook Networks Ltd. – Business Card</title>
<link rel="stylesheet" href="https://fonts.googleapis.com/css2?family=Source+Sans+3:ital,wght@0,400;0,600;1,600&display=swap">
<style>
  :root {
    --brand-blue: #18a7e4;
    --ink-grey: #58595b;
    --card-white: #ffffff;
    --card-back: #5f6062;
    --backdrop: #3b3b3d;
    --text-light: #ffffff;
  }
  * { margin: 0; padding: 0; box-sizing: border-box; }
  html, body {
    width: 1105px;
    height: 1200px;
    overflow: hidden;
    background: var(--backdrop);
    font-family: "Source Sans 3", sans-serif;
  }
  .canvas {
    position: relative;
    width: 1105px;
    height: 1200px;
  }
  .card {
    position: absolute;
    left: 196px;
    width: 720px;
    height: 412px;
    overflow: hidden;
  }
  .card--front { top: 145px; background: var(--card-white); }
  .card--back  { top: 602px; background: var(--card-back); }

  /* Front */
  .wordmark {
    position: absolute;
    left: 56px;
    top: 72px;
    display: flex;
    align-items: center;
    gap: 14px;
  }
  .wordmark__dot {
    width: 22px;
    height: 22px;
    border-radius: 50%;
    background: var(--brand-blue);
  }
  .wordmark__name {
    font-weight: 600;
    font-size: 34px;
    color: var(--brand-blue);
    letter-spacing: 0.2px;
  }
  .contact-panel {
    position: absolute;
    inset: 0;
    width: 720px;
    height: 412px;
  }
  .contact-panel polygon { fill: var(--brand-blue); }
  .contact {
    position: absolute;
    right: 28px;
    top: 184px;
    text-align: right;
    color: var(--text-light);
  }
  .contact__name {
    font-weight: 600;
    font-size: 31px;
    line-height: 1;
    margin-bottom: 16px;
  }
  .contact__address {
    font-size: 19px;
    line-height: 26px;
    margin-bottom: 8px;
  }
  .contact__line {
    display: flex;
    justify-content: flex-end;
    align-items: center;
    gap: 12px;
    font-size: 19px;
    line-height: 27.5px;
  }
  .contact__icon {
    width: 16px;
    height: 16px;
    flex: none;
  }

  /* Back */
  .back-mark {
    position: absolute;
    left: 0;
    right: 0;
    top: 176px;
    display: flex;
    justify-content: center;
    align-items: center;
    gap: 14px;
  }
  .back-mark__square {
    width: 26px;
    height: 26px;
    border: 3px solid var(--text-light);
  }
  .back-mark__name {
    font-weight: 600;
    font-size: 44px;
    color: var(--text-light);
  }
  .tagline {
    position: absolute;
    left: 0;
    right: 0;
    top: 340px;
    text-align: center;
    font-style: italic;
    font-weight: 600;
    font-size: 18px;
    letter-spacing: 0.4px;
    color: var(--text-light);
  }
</style>
</head>
<body>
<main class="canvas">

  <section class="card card--front" aria-label="Business card front">
    <svg class="contact-panel" viewBox="0 0 720 412" aria-hidden="true">
      <polygon points="490,148 694,148 720,196 720,412 439,412 389,322"/>
    </svg>

    <div class="wordmark">
      <span class="wordmark__dot"></span>
      <span class="wordmark__name">Quillbrook Networks Ltd.</span>
    </div>

    <div class="contact">
      <p class="contact__name">Dana Whitfield</p>
      <p class="contact__address">214 Cedarholm Road<br>Burnaby, BC V5G 1K4</p>
      <p class="contact__line">604-555-0148
        <svg class="contact__icon" viewBox="0 0 16 16" aria-hidden="true"><path fill="#fff" d="M3.2 1.2l2.4 0 1.1 3.3-1.6 1.2c.8 1.8 2.4 3.4 4.2 4.2l1.2-1.6 3.3 1.1v2.4c0 .9-.8 1.6-1.7 1.5C6.3 12.8 2.2 8.7 1.7 2.9 1.6 2 2.3 1.2 3.2 1.2z"/></svg>
      </p>
      <p class="contact__line">dwhitfield@quillbrook.me
        <svg class="contact__icon" viewBox="0 0 16 16" aria-hidden="true"><rect x="1" y="3.5" width="14" height="9.5" fill="#fff"/><path d="M1.5 4l6.5 5 6.5-5" fill="none" stroke="#18a7e4" stroke-width="1.3"/></svg>
      </p>
      <p class="contact__line">www.quillbrook.me
        <svg class="contact__icon" viewBox="0 0 16 16" aria-hidden="true"><circle cx="8" cy="8" r="7" fill="#fff"/><g fill="none" stroke="#18a7e4" stroke-width="1.1"><ellipse cx="8" cy="8" rx="3" ry="7"/><path d="M1 8h14M2.5 4.5h11M2.5 11.5h11"/></g></svg>
      </p>
    </div>
  </section>

  <section class="card card--back" aria-label="Business card back">
    <div class="back-mark">
      <span class="back-mark__square"></span>
      <span class="back-mark__name">Quillbrook</span>
    </div>
    <p class="tagline">Revolutionizing IT Services</p>
  </section>

</main>
</body>
</html>
```